Landing Page & Logo for Over 50s Guaranteed Life Cover

www.ripeyearsquote.com provides a method of comparing guaranteed life cover for consumers aged over 50. The approach we are initially looking to deploy is a simple landing page that provides the user with high level information about over 50s plans and allows them to see which provider is offering the best deal by ranking providers in a table. This will compare costs / core features in the same way as shown in the attached file.

The page should incorporate a new logo design for RipeYearsQuote.com which should be similar in design to the website maplegreyhub.com.

Key elements of the landing page include:

Header (incorporating new logo and strapline e.g. "helping you find the best cover at the best price")
Introductory Text (to allow brief description of the service)
Comparison Table (to show top 10 providers - to include logos)
Table Links (allows customer to link directly from the table to the providers site)
Helpline (details of helpline number 0800 617 2948 - not actual number)
Join The Club (allows customers to sign up - using their email - to the over 50s club for more information and offers)

Other design elements welcomed to ensure the landing page is simple to understand, easy to navigate, visually appealing, focused on driving action / sales.
Updates

Target Market(s)

50 - 80

Industry/Entity Type

Insurance

Logo Text

ripeyearsquote and strapline "helping you find the best cover at the best price"

Number of Pages Required

1 page

Font styles to use
Sans Serif

Colors
a5ce39
add136
cadf82
eaf2ce
ffffff

Requirements
Nice to have
• Ideally created so content can be managed via WordPress.

```html
<!DOCTYPE html>
<html lang="en">
<head>
<meta charset="utf-8">
<title>Ripe Years Quote – Over 50s Life Cover Comparison</title>
<link rel="stylesheet" href="https://fonts.googleapis.com/css2?family=Open+Sans:ital,wght@0,300;0,400;0,600;0,700;1,400&family=Ubuntu:wght@400;500;700&display=swap">
<style>
:root{
  --green:#a5ce39;
  --green-2:#add136;
  --green-soft:#cadf82;
  --green-pale:#eaf2ce;
  --white:#ffffff;
  --ink:#333333;
  --ink-soft:#666666;
  --line:#e4e4e4;
  --panel:#eeeeee;
  --dark:#333333;
  --darker:#262626;
  --field:#222222;
  --btn-dark:#4a4a4a;
}
*{box-sizing:border-box;margin:0;padding:0}
html,body{width:1200px;height:2894px;overflow:hidden}
body{position:relative;background:var(--white);font-family:'Open Sans',Arial,sans-serif;color:var(--ink)}

/* top bar */
.topbar{position:absolute;left:0;top:0;width:1200px;height:35px;background:var(--green);color:var(--white);font-size:12px}
.topbar .strapline{position:absolute;left:92px;top:9px;font-weight:600}
.topbar .helpline{position:absolute;right:123px;top:8px;font-size:13px}
.topbar .retrieve{position:absolute;right:59px;top:0;height:35px;width:120px;background:#2d2d2d;color:var(--white);font-size:11px;font-weight:700;text-align:center;line-height:35px;right:57px}
.topbar .helpline{right:190px}

/* header */
.site-header{position:absolute;left:0;top:35px;width:1200px;height:112px;background:var(--white);border-bottom:4px solid #d7d7d7}
.brand{position:absolute;left:98px;top:37px;font-family:'Ubuntu',sans-serif;font-weight:700;font-size:29px;letter-spacing:1px;color:#2f2f2f}
.main-nav{position:absolute;right:95px;top:47px;display:flex;gap:28px;font-size:12.5px;color:#444;text-transform:uppercase}
.main-nav .active{color:var(--green)}
.main-nav svg{margin-top:1px}

/* hero */
.hero{position:absolute;left:0;top:147px;width:1200px;height:523px;background:linear-gradient(180deg,#e7e3df 0%,#d8cfc6 45%,#b7a697 75%,#8f7f72 100%)}
.hero-title{position:absolute;left:98px;top:200px;color:var(--white);font-size:48px;line-height:60px;text-shadow:0 2px 6px rgba(0,0,0,.35);text-transform:uppercase}
.hero-title strong{display:block;font-weight:700}
.hero-title span{display:block;font-weight:300}
.hero-arrow{position:absolute;top:228px}
.hero-bump{position:absolute;left:561px;top:487px;width:78px;height:78px;border-radius:50%;background:var(--white)}
.hero-bump svg{position:absolute;left:29px;top:18px}

/* welcome */
.welcome{position:absolute;left:0;top:670px;width:1200px;height:420px;background:var(--white);text-align:center}
.section-title{font-family:'Ubuntu',sans-serif;font-size:26px;font-weight:400;color:var(--ink);text-transform:uppercase}
.section-title em{font-style:normal;color:var(--green)}
.welcome .section-title{position:absolute;left:0;width:1200px;top:42px}
.welcome .intro{position:absolute;left:105px;width:990px;top:96px;font-size:11px;line-height:24px;color:#555}
.services{position:absolute;left:0;top:188px;width:1200px}
.service{position:absolute;width:230px;text-align:center}
.service .icon{width:90px;height:90px;border-radius:50%;border:2px solid #333;margin:0 auto;display:flex;align-items:center;justify-content:center}
.service.is-active .icon{border-color:var(--green)}
.service h3{margin-top:38px;font-size:13px;font-weight:400;color:#333;text-transform:uppercase}
.service.is-active h3{color:var(--green)}
.service p{margin-top:10px;font-size:11px;line-height:24px;color:#555;padding:0 22px}
.slide-arrow{position:absolute;top:265px}

/* comparison */
.comparison{position:absolute;left:0;top:1090px;width:1200px;height:1478px;background:var(--panel)}
.comparison .section-title{position:absolute;left:0;width:1200px;top:28px;text-align:center}
.compare-table{position:absolute;left:98px;top:97px;width:1004px;border-collapse:collapse;table-layout:fixed;background:var(--white);box-shadow:0 1px 3px rgba(0,0,0,.12);font-family:'Ubuntu',sans-serif}
.compare-table th{height:84px;background:linear-gradient(180deg,#b3d653 0%,var(--green) 55%,#97c02c 100%);color:var(--white);font-weight:400;font-size:13.5px;border-right:1px solid rgba(255,255,255,.35)}
.compare-table th:last-child{border-right:0}
.compare-table td{height:125.8px;border-right:1px solid var(--line);border-bottom:1px solid var(--line);text-align:center;vertical-align:top}
.compare-table td:last-child{border-right:0}
.compare-table tr:last-child td{border-bottom:0}
.value{display:block;margin-top:30px;font-size:19px;font-weight:500;color:#333}
.info{display:inline-block;margin-top:10px;width:20px;height:20px;border-radius:50%;background:var(--green);color:var(--white);font-family:'Open Sans',sans-serif;font-weight:700;font-size:13px;line-height:20px}
.provider{display:flex;align-items:center;justify-content:center;margin:24px auto 0;width:113px;height:77px;border:1px solid #d9d9d9;border-radius:4px;font-family:'Open Sans',sans-serif;font-size:12px;font-weight:600;color:#555;line-height:15px}
.btn{display:flex;justify-content:space-between;align-items:center;width:110px;height:34px;margin:0 auto;padding:0 12px;border-radius:3px;font-size:14px;color:var(--white);font-family:'Ubuntu',sans-serif}
.btn-buy{margin-top:24px;background:var(--btn-dark)}
.btn-info{margin-top:10px;background:var(--green)}
.btn i{font-style:normal;font-size:15px}

/* footer */
.site-footer{position:absolute;left:0;top:2568px;width:1200px;height:256px;background:var(--dark);color:#cfcfcf}
.site-footer h4{position:absolute;font-family:'Ubuntu',sans-serif;font-weight:400;font-size:15px;color:var(--green);text-transform:uppercase}
.join h4{left:98px;top:42px;font-size:17px}
.field{position:absolute;background:var(--field);color:#ddd;font-size:10px;padding:10px 14px}
.signup{position:absolute;left:351px;top:164px;width:230px;height:39px;background:var(--green);color:var(--white);font-size:13px;font-weight:600;text-align:center;line-height:39px}
.footer-links{position:absolute;left:640px;top:80px;list-style:none;font-size:11px;line-height:24.5px;color:#cfcfcf}
.address{position:absolute;left:780px;top:76px;width:200px;font-size:11px;line-height:24.5px}
.social{position:absolute;left:996px;top:74px;list-style:none;font-size:11px}
.social li{display:flex;align-items:center;gap:8px;height:37px}
.social .dot{width:26px;height:26px;border-radius:50%;background:#5a5a5a}
.copyright{position:absolute;left:0;top:2824px;width:1200px;height:70px;background:var(--darker);color:#bbb;font-size:11px;text-align:center;line-height:70px}
</style>
</head>
<body>

<div class="topbar">
  <span class="strapline">" Helping you find the best cover at the best price "</span>
  <span class="helpline">Helpline number : 0800 617 2948</span>
  <span class="retrieve">RETRIEVE A QUOTE</span>
</div>

<header class="site-header">
  <div class="brand">RIPE YEARS QUOTE</div>
  <nav class="main-nav">
    <span class="active">Home</span><span>Car</span><span>Travel</span><span>Pet</span><span>Caravan</span><span>Life</span><span>Health</span><span>Income Protection</span>
    <svg width="13" height="13" viewBox="0 0 13 13"><circle cx="5.5" cy="5.5" r="4" fill="none" stroke="#a5ce39" stroke-width="2"/><line x1="8.5" y1="8.5" x2="12" y2="12" stroke="#a5ce39" stroke-width="2"/></svg>
  </nav>
</header>

<section class="hero" role="img" aria-label="Photo of two hands sheltering a small model house with a red roof">
  <h1 class="hero-title"><strong>An insurance comparison</strong><span>site for the over 50's.</span></h1>
  <svg class="hero-arrow" style="left:30px" width="16" height="30" viewBox="0 0 16 30"><polyline points="14,2 2,15 14,28" fill="none" stroke="#fff" stroke-width="2.5" opacity=".8"/></svg>
  <svg class="hero-arrow" style="right:30px" width="16" height="30" viewBox="0 0 16 30"><polyline points="2,2 14,15 2,28" fill="none" stroke="#fff" stroke-width="2.5" opacity=".8"/></svg>
  <div class="hero-bump"><svg width="20" height="12" viewBox="0 0 20 12"><polyline points="1,11 10,2 19,11" fill="none" stroke="#bbb" stroke-width="2"/></svg></div>
</section>

<section class="welcome">
  <h2 class="section-title"><em>Welcome to</em> our company</h2>
  <p class="intro">We compare guaranteed life cover from leading providers for people aged over fifty, so you can see clearly who offers the best price. Every plan shown accepts applicants without medical questions, and each quote sets out the cover amount, monthly premium and total cost in plain terms. Browse the table below, read more about each plan, then apply directly with your chosen provider in a few simple steps.</p>
  <svg class="slide-arrow" style="left:38px" width="16" height="32" viewBox="0 0 16 32"><polyline points="14,2 2,16 14,30" fill="none" stroke="#ccc" stroke-width="2"/></svg>
  <svg class="slide-arrow" style="right:38px" width="16" height="32" viewBox="0 0 16 32"><polyline points="2,2 14,16 2,30" fill="none" stroke="#ccc" stroke-width="2"/></svg>
  <div class="services">
    <div class="service is-active" style="left:85px">
      <div class="icon"><svg width="30" height="28" viewBox="0 0 30 28"><path d="M15 2 L28 14 H24 V26 H18 V18 H12 V26 H6 V14 H2 Z" fill="#a5ce39"/></svg></div>
      <h3>Home Insurance</h3>
      <p>Protect the home you have worked so hard for</p>
    </div>
    <div class="service" style="left:348px">
      <div class="icon"><svg width="32" height="24" viewBox="0 0 32 24"><path d="M6 4 Q7 1 10 1 H22 Q25 1 26 4 L29 11 Q31 12 31 15 V21 H27 V24 H22 V21 H10 V24 H5 V21 H1 V15 Q1 12 3 11 Z M7 11 H25 L23 5 H9 Z" fill="#333"/><circle cx="7" cy="16" r="2" fill="#fff"/><circle cx="25" cy="16" r="2" fill="#fff"/></svg></div>
      <h3>Car Insurance</h3>
      <p>Fair cover for careful drivers with experience</p>
    </div>
    <div class="service" style="left:612px">
      <div class="icon"><svg width="30" height="26" viewBox="0 0 30 26"><rect x="1" y="6" width="28" height="19" rx="2" fill="#333"/><rect x="10" y="1" width="10" height="6" rx="1" fill="none" stroke="#333" stroke-width="2"/><rect x="1" y="13" width="28" height="2" fill="#fff"/><rect x="13" y="11" width="4" height="6" fill="#fff"/></svg></div>
      <h3>Travel Insurance</h3>
      <p>Trips abroad covered with no upper age limit</p>
    </div>
    <div class="service" style="left:876px">
      <div class="icon"><svg width="28" height="26" viewBox="0 0 28 26"><ellipse cx="14" cy="18" rx="7" ry="6" fill="#333"/><ellipse cx="5" cy="11" rx="3" ry="4" fill="#333"/><ellipse cx="23" cy="11" rx="3" ry="4" fill="#333"/><ellipse cx="10" cy="4" rx="3" ry="4" fill="#333"/><ellipse cx="18" cy="4" rx="3" ry="4" fill="#333"/></svg></div>
      <h3>Pet Insurance</h3>
      <p>Vet bills covered for your loyal companions</p>
    </div>
  </div>
</section>

<section class="comparison">
  <h2 class="section-title"><em>Comparison</em> table</h2>
  <table class="compare-table">
    <thead>
      <tr><th>Company Name</th><th>Cover Amount</th><th>Premium</th><th>Payment Term</th><th>Total Payment</th><th>Initial Period</th><th>Buy Now</th></tr>
    </thead>
    <tbody>
      <tr><td><div class="provider">Arrowmark</div></td><td><span class="value">£ 4,200</span><span class="info">i</span></td><td><span class="value">£10.00</span><span class="info">i</span></td><td><span class="value">40 Years</span><span class="info">i</span></td><td><span class="value">£4,800.00</span><span class="info">i</span></td><td><span class="value">24 Month</span><span class="info">i</span></td><td><a class="btn btn-buy">Buy <i>»</i></a><a class="btn btn-info">More Info <i>»</i></a></td></tr>
      <tr><td><div class="provider">Trio Assure</div></td><td><span class="value">£ 4,200</span><span class="info">i</span></td><td><span class="value">£10.00</span><span class="info">i</span></td><td><span class="value">40 Years</span><span class="info">i</span></td><td><span class="value">£4,800.00</span><span class="info">i</span></td><td><span class="value">24 Month</span><span class="info">i</span></td><td><a class="btn btn-buy">Buy <i>»</i></a><a class="btn btn-info">More Info <i>»</i></a></td></tr>
      <tr><td><div class="provider">Umbrella Kin</div></td><td><span class="value">£ 4,200</span><span class="info">i</span></td><td><span class="value">£10.00</span><span class="info">i</span></td><td><span class="value">40 Years</span><span class="info">i</span></td><td><span class="value">£4,800.00</span><span class="info">i</span></td><td><span class="value">24 Month</span><span class="info">i</span></td><td><a class="btn btn-buy">Buy <i>»</i></a><a class="btn btn-info">More Info <i>»</i></a></td></tr>
      <tr><td><div class="provider">Brightvale</div></td><td><span class="value">£ 4,200</span><span class="info">i</span></td><td><span class="value">£10.00</span><span class="info">i</span></td><td><span class="value">40 Years</span><span class="info">i</span></td><td><span class="value">£4,800.00</span><span class="info">i</span></td><td><span class="value">24 Month</span><span class="info">i</span></td><td><a class="btn btn-buy">Buy <i>»</i></a><a class="btn btn-info">More Info <i>»</i></a></td></tr>
      <tr><td><div class="provider">Hexa Life</div></td><td><span class="value">£ 4,200</span><span class="info">i</span></td><td><span class="value">£10.00</span><span class="info">i</span></td><td><span class="value">40 Years</span><span class="info">i</span></td><td><span class="value">£4,800.00</span><span class="info">i</span></td><td><span class="value">24 Month</span><span class="info">i</span></td><td><a class="btn btn-buy">Buy <i>»</i></a><a class="btn btn-info">More Info <i>»</i></a></td></tr>
      <tr><td><div class="provider">Leafline</div></td><td><span class="value">£ 4,200</span><span class="info">i</span></td><td><span class="value">£10.00</span><span class="info">i</span></td><td><span class="value">40 Years</span><span class="info">i</span></td><td><span class="value">£4,800.00</span><span class="info">i</span></td><td><span class="value">24 Month</span><span class="info">i</span></td><td><a class="btn btn-buy">Buy <i>»</i></a><a class="btn btn-info">More Info <i>»</i></a></td></tr>
      <tr><td><div class="provider">Kinfold</div></td><td><span class="value">£ 4,200</span><span class="info">i</span></td><td><span class="value">£10.00</span><span class="info">i</span></td><td><span class="value">40 Years</span><span class="info">i</span></td><td><span class="value">£4,800.00</span><span class="info">i</span></td><td><span class="value">24 Month</span><span class="info">i</span></td><td><a class="btn btn-buy">Buy <i>»</i></a><a class="btn btn-info">More Info <i>»</i></a></td></tr>
      <tr><td><div class="provider">Orbit Assure</div></td><td><span class="value">£ 4,200</span><span class="info">i</span></td><td><span class="value">£10.00</span><span class="info">i</span></td><td><span class="value">40 Years</span><span class="info">i</span></td><td><span class="value">£4,800.00</span><span class="info">i</span></td><td><span class="value">24 Month</span><span class="info">i</span></td><td><a class="btn btn-buy">Buy <i>»</i></a><a class="btn btn-info">More Info <i>»</i></a></td></tr>
      <tr><td><div class="provider">Homestead</div></td><td><span class="value">£ 4,200</span><span class="info">i</span></td><td><span class="value">£10.00</span><span class="info">i</span></td><td><span class="value">40 Years</span><span class="info">i</span></td><td><span class="value">£4,800.00</span><span class="info">i</span></td><td><span class="value">24 Month</span><span class="info">i</span></td><td><a class="btn btn-buy">Buy <i>»</i></a><a class="btn btn-info">More Info <i>»</i></a></td></tr>
      <tr><td><div class="provider">Rosewell</div></td><td><span class="value">£ 4,200</span><span class="info">i</span></td><td><span class="value">£10.00</span><span class="info">i</span></td><td><span class="value">40 Years</span><span class="info">i</span></td><td><span class="value">£4,800.00</span><span class="info">i</span></td><td><span class="value">24 Month</span><span class="info">i</span></td><td><a class="btn btn-buy">Buy <i>»</i></a><a class="btn btn-info">More Info <i>»</i></a></td></tr>
    </tbody>
  </table>
</section>

<footer class="site-footer">
  <div class="join">
    <h4>Join the club</h4>
    <div class="field" style="left:100px;top:91px;width:232px;height:35px">Name</div>
    <div class="field" style="left:100px;top:135px;width:232px;height:35px">Email</div>
    <div class="field" style="left:100px;top:181px;width:232px;height:35px">Subject</div>
    <div class="field" style="left:351px;top:91px;width:230px;height:62px">Message</div>
    <div class="signup">SIGN UP</div>
  </div>
  <h4 style="left:640px;top:46px;font-size:13px">Welcome</h4>
  <ul class="footer-links"><li>Home</li><li>Car</li><li>Travel</li><li>Pet</li><li>Income Protection</li></ul>
  <h4 style="left:780px;top:42px;font-size:17px">Address</h4>
  <p class="address">14 Orchard Row, Halden Street, Marlow Park, Leeds LS2 7QT</p>
  <h4 style="left:996px;top:46px;font-size:13px">Follow us</h4>
  <ul class="social">
    <li><span class="dot"></span>: Friendwall</li>
    <li><span class="dot"></span>: Chirpline</li>
    <li><span class="dot"></span>: Workring</li>
    <li><span class="dot"></span>: Circlecast</li>
  </ul>
</footer>
<div class="copyright">Copyrights 2016. maplegreyhub.com . All rights reserved.</div>

</body>
</html>
```